Dalvick's Business Card

I need some designs for a new business card including the new logo attached. An old example of our business card is also attached to show all the data that should be included on the new design.
**I added some more examples someone had mocked up**

Contact Information for Business Card

Should include all info on other examples uploaded.

```html
<!DOCTYPE html>
<html lang="en">
<head>
<meta charset="utf-8">
<title>Dalvick's Business Card</title>
<link href="https://fonts.googleapis.com/css2?family=Montserrat:wght@300;400;600;700;800&family=Roboto+Condensed:ital,wght@1,800&display=swap" rel="stylesheet">
<style>
  :root{
    --blue:#0a6fc2;
    --red:#ec1c24;
    --white:#ffffff;
    --ink:#1a1a1a;
    --rule:#9cc6ea;
    --bg:#2b2b2b;
  }
  *{box-sizing:border-box;margin:0;padding:0}
  html,body{width:1200px;height:866px;overflow:hidden;background:var(--bg)}
  body{font-family:'Montserrat',sans-serif;position:relative}
  .card{position:absolute;left:250px;width:700px;height:400px;overflow:hidden;box-shadow:0 6px 18px rgba(0,0,0,.45)}
  .card-front{top:22px;background:var(--white)}
  .card-back{top:444px;background:var(--blue)}

  /* front */
  .owner{position:absolute;left:40px;top:86px;width:230px}
  .owner-name{color:var(--blue);font-weight:800;font-size:25px;letter-spacing:1px;text-transform:uppercase;padding-bottom:10px;border-bottom:1px solid var(--rule)}
  .contact{list-style:none;margin-top:14px}
  .contact li{display:flex;align-items:center;gap:10px;font-size:17px;color:var(--ink);margin-bottom:6px}
  .contact svg{flex:none}
  .brand{position:absolute;left:300px;top:100px}
  .brand-name{display:flex;align-items:center;gap:12px;color:var(--blue);font-weight:800;font-size:58px;letter-spacing:2px;line-height:1}
  .brand-dot{width:34px;height:34px;border-radius:50%;background:var(--red)}
  .brand-tag{color:var(--red);font-weight:600;font-size:13.5px;letter-spacing:1.6px;margin:6px 0 0 48px;text-transform:uppercase}
  .guide{position:absolute;left:40px;right:40px;height:1px;background:var(--rule)}
  .guide-1{top:262px}
  .bands{position:absolute;left:0;bottom:0;width:700px;height:96px}
  .band-text{position:absolute;color:var(--white);font-weight:700;text-transform:uppercase;letter-spacing:1.5px}
  .band-licensed{left:40px;bottom:38px;font-size:16px}
  .band-family{right:40px;bottom:18px;font-size:19px}

  /* back */
  .back-art{position:absolute;left:0;top:0}
  .back-mark{position:absolute;left:70px;top:170px;display:flex;align-items:center;gap:10px;color:var(--white);font-weight:800;font-size:34px;letter-spacing:1.5px}
  .back-mark span.dot{width:22px;height:22px;border-radius:50%;background:var(--white)}
  .pitch{position:absolute;right:46px;top:70px;width:290px;text-align:right}
  .pitch-head{font-family:'Roboto Condensed',sans-serif;font-style:italic;font-weight:800;color:var(--white);font-size:33px;line-height:1.08;text-transform:uppercase}
  .pitch-rule{height:1.5px;background:var(--white);margin:18px 0 14px 30px}
  .pitch-area{color:var(--white);font-weight:400;font-size:19px;line-height:1.2;text-align:left;padding-left:30px}
</style>
</head>
<body>

<section class="card card-front" aria-label="Business card front">
  <div class="owner">
    <h2 class="owner-name">Mark Dalvick</h2>
    <ul class="contact">
      <li>
        <svg width="18" height="18" viewBox="0 0 24 24" aria-hidden="true"><path fill="var(--red)" d="M6.6 10.8a15.1 15.1 0 0 0 6.6 6.6l2.2-2.2c.3-.3.7-.4 1-.2 1.1.4 2.3.6 3.6.6.6 0 1 .4 1 1V20c0 .6-.4 1-1 1A17 17 0 0 1 3 4c0-.6.4-1 1-1h3.5c.6 0 1 .4 1 1 0 1.3.2 2.5.6 3.6.1.3 0 .7-.2 1z"/></svg>
        555.014.2290
      </li>
      <li>
        <svg width="18" height="14" viewBox="0 0 24 18" aria-hidden="true"><rect width="24" height="18" rx="2" fill="var(--red)"/><path d="M1 2l11 8 11-8" stroke="var(--white)" stroke-width="2" fill="none"/></svg>
        hvacdalvick@mailbox.com
      </li>
    </ul>
  </div>

  <div class="brand">
    <div class="brand-name"><span class="brand-dot"></span>DALVICK'S</div>
    <p class="brand-tag">Air Conditioning &amp; Heating Service</p>
  </div>

  <div class="guide guide-1"></div>

  <svg class="bands" viewBox="0 0 700 96" aria-hidden="true">
    <path d="M0 34 L700 34 L700 96 L0 96 Z" fill="var(--blue)"/>
    <path d="M0 28 L270 28 C300 28 300 62 330 62 L0 62 Z" fill="var(--red)"/>
    <path d="M0 62 L330 62 C300 62 300 28 270 28 L700 28 L700 34 L0 34 Z" fill="var(--white)" opacity="0"/>
    <path d="M270 22 C310 22 305 58 345 58 L700 58" stroke="var(--white)" stroke-width="4" fill="none"/>
  </svg>
  <span class="band-text band-licensed">Licensed &amp; Insured</span>
  <span class="band-text band-family">Family Owned &amp; Operated</span>
</section>

<section class="card card-back" aria-label="Business card back">
  <svg class="back-art" width="700" height="400" viewBox="0 0 700 400" aria-hidden="true">
    <path d="M0 0 L260 0 C200 120 150 260 0 330 Z" fill="var(--red)"/>
  </svg>
  <div class="back-mark"><span class="dot"></span>DALVICK'S</div>

  <div class="pitch">
    <p class="pitch-head">Call today for<br>all your HVAC,<br>refrigeration &amp;<br>plumbing needs</p>
    <div class="pitch-rule"></div>
    <p class="pitch-area">Serves Maplewood<br>IA &amp; Surrounding<br>Areas</p>
  </div>
</section>

</body>
</html>
```